Indy Film Production Company/Studio

We need a business card designed from an existing logo. We are a digital studio/production company that caters to creating genre entertainment, like Action, Horror, and martial arts. The card along with the logo will be used to Brand the company from letter heads to banners. The design will also be used for postcards and Brochures. It should be professional and masculine.
Updates

Thank you to all the designers who have participated. I'm narrowing down who it will be. Thank you again.

Target Market(s)

Investors, Networks, Producers, and actors

Industry/Entity Type

Film Production

Contact Information for Business Card

Teodoro Valbuena
Producer/Writer/Director
www.kestrelpicturehouse.example

Requirements
Must have
• Website address, Facebook icon and Twitter icon possibly in the back of the card.
Nice to have
• Logline of Company: Follow The Action.

```html
<!DOCTYPE html>
<html lang="en">
<head>
<meta charset="utf-8">
<title>Kestrel Picture House — Business Card</title>
<link rel="stylesheet" href="https://fonts.googleapis.com/css2?family=Montserrat:wght@300;400;800&display=swap">
<style>
  :root {
    --backdrop: #2b2927;
    --card-black: #141414;
    --card-white: #f3f3f3;
    --ink-black: #111111;
    --ink-silver: #c9c9c9;
    --ink-grey: #8a8a8a;
    --camera-dark: #3a3a3c;
    --camera-light: #d8d8d8;
  }
  * { box-sizing: border-box; margin: 0; padding: 0; }
  html, body {
    width: 1200px; height: 727px; overflow: hidden;
    background: var(--backdrop);
    font-family: "Montserrat", sans-serif;
  }
  .stage {
    position: relative; width: 1200px; height: 727px;
    display: flex; align-items: center; justify-content: center; gap: 60px;
  }
  .card {
    position: relative; width: 500px; height: 286px;
    border-radius: 4px; overflow: hidden;
    box-shadow: 0 14px 30px rgba(0,0,0,.45);
  }
  /* Back of card */
  .card--back { background: var(--card-black); color: var(--ink-silver); }
  .card--back .brand-name {
    position: absolute; left: 0; right: 0; top: 92px;
    text-align: center; font-weight: 800; font-size: 30px;
    letter-spacing: 1px; text-transform: uppercase; color: var(--ink-silver);
  }
  .card--back .website {
    position: absolute; left: 0; right: 0; top: 152px;
    text-align: center; font-weight: 400; font-size: 13px; color: var(--ink-silver);
  }
  .social {
    position: absolute; right: 22px; bottom: 20px; display: flex; gap: 6px;
  }
  .social-square { width: 20px; height: 20px; border-radius: 3px; background: var(--ink-silver); }

  /* Front of card */
  .card--front { background: var(--card-white); color: var(--ink-black); }
  .card--front .brand-name {
    position: absolute; left: 30px; top: 30px;
    font-weight: 800; font-size: 20px; line-height: 1.05;
    text-transform: uppercase; color: var(--ink-black); width: 180px;
  }
  .person { position: absolute; left: 30px; top: 140px; }
  .person-name { font-weight: 400; font-size: 20px; color: var(--ink-black); }
  .person-role { font-weight: 300; font-size: 13px; margin-top: 3px; color: #333; }
  .camera-photo {
    position: absolute; right: 18px; bottom: 0; width: 210px; height: 175px;
    border-radius: 6px 6px 0 0;
    background: radial-gradient(ellipse at 55% 55%, var(--camera-dark) 0%, #5a5a5c 45%, var(--camera-light) 78%, transparent 100%);
  }
</style>
</head>
<body>
<main class="stage">
  <section class="card card--back" aria-label="Business card, back">
    <p class="brand-name">Kestrel Picture House</p>
    <p class="website">www.kestrelpicturehouse.example</p>
    <div class="social">
      <span class="social-square" aria-label="Social profile"></span>
      <span class="social-square" aria-label="Social profile"></span>
    </div>
  </section>

  <section class="card card--front" aria-label="Business card, front">
    <p class="brand-name">Kestrel Picture House</p>
    <div class="person">
      <p class="person-name">Teodoro Valbuena</p>
      <p class="person-role">Producer/Writer/Director</p>
    </div>
    <div class="camera-photo" role="img" aria-label="Photo of a professional cinema camera rig on a tripod"></div>
  </section>
</main>
</body>
</html>
```